business card design for a plumbing contractor

i need a double business card for a plumbing business, our initial service is residential Sewer Drain Cleaning.

Target Market(s)

other plumbing Business

Industry/Entity Type

Plumbing

Contact Information for Business Card

www.PipeworksTopMark.example- 5307218394-

Font styles to use
Serif

Colors
ec1f27
0455a3

```html
<!DOCTYPE html>
<html lang="en">
<head>
<meta charset="UTF-8">
<title>Pipeworks Top Mark – Business Card</title>
<link rel="stylesheet" href="https://fonts.googleapis.com/css2?family=Roboto+Slab:wght@300;400;800&display=swap">
<style>
  :root {
    --backdrop: #2b2b2b;
    --card: #1b1b1c;
    --card-edge: #242425;
    --silver: #d4d4d4;
    --text-soft: #b0b0b0;
    --emboss: #111112;
    --brand-red: #ec1f27;
    --brand-blue: #0455a3;
  }
  * { margin: 0; padding: 0; box-sizing: border-box; }
  html, body { width: 1200px; height: 900px; overflow: hidden; }
  body {
    background: var(--backdrop);
    font-family: "Roboto Slab", Georgia, serif;
    display: flex;
    flex-direction: column;
    align-items: center;
    justify-content: center;
    gap: 44px;
  }
  .card {
    width: 640px;
    height: 366px;
    background: var(--card);
    border: 1px solid var(--card-edge);
    box-shadow: 0 12px 30px rgba(0,0,0,0.45);
    position: relative;
    overflow: hidden;
  }
  /* front */
  .card-front { display: flex; align-items: center; justify-content: center; }
  .brand { display: flex; align-items: center; gap: 14px; }
  .brand-name {
    font-weight: 800;
    line-height: 1;
    letter-spacing: -0.5px;
  }
  .card-front .brand-name { font-size: 46px; color: var(--silver); }
  .brand-mark { width: 34px; height: 34px; background: var(--brand-red); flex: none; }
  /* back */
  .card-back { display: flex; align-items: center; padding: 0 30px; }
  .back-brand { width: 200px; flex: none; }
  .card-back .brand { gap: 10px; }
  .card-back .brand-name { font-size: 27px; color: var(--emboss); text-shadow: 0 1px 0 #262627; }
  .card-back .brand-mark { width: 20px; height: 20px; background: var(--brand-red); }
  .divider { width: 1px; height: 250px; background: var(--brand-blue); margin: 0 20px 0 10px; flex: none; }
  .details { color: var(--silver); flex: 1; min-width: 0; white-space: nowrap; }
  .person-name { font-size: 23px; font-weight: 400; letter-spacing: 1px; }
  .person-role { font-size: 14px; font-weight: 300; color: var(--text-soft); margin-bottom: 16px; }
  .contact-list, .service-list { list-style: none; }
  .contact-item {
    display: flex; align-items: center; gap: 8px;
    font-size: 14px; font-weight: 300; line-height: 1.6;
  }
  .contact-item svg { width: 11px; height: 11px; fill: var(--brand-blue); flex: none; }
  .service-list { margin-top: 10px; }
  .service-item {
    font-size: 14px; font-weight: 300; line-height: 1.5;
    display: flex; align-items: center; gap: 11px;
  }
  .service-item::before {
    content: ""; width: 5px; height: 5px; border-radius: 50%;
    background: var(--brand-red); flex: none;
  }
</style>
</head>
<body>
  <section class="card card-front">
    <div class="brand">
      <div class="brand-name">Pipeworks<br>Top Mark</div>
      <div class="brand-mark"></div>
    </div>
  </section>

  <section class="card card-back">
    <div class="back-brand">
      <div class="brand">
        <div class="brand-name">Pipeworks<br>Top Mark</div>
        <div class="brand-mark"></div>
      </div>
    </div>
    <div class="divider"></div>
    <div class="details">
      <h1 class="person-name">DORIAN KELLER</h1>
      <p class="person-role">Director</p>
      <ul class="contact-list">
        <li class="contact-item">
          <svg viewBox="0 0 24 24"><path d="M6.6 10.8a15.1 15.1 0 0 0 6.6 6.6l2.2-2.2c.3-.3.7-.4 1-.2 1.1.4 2.3.6 3.6.6.6 0 1 .4 1 1V20c0 .6-.4 1-1 1A17 17 0 0 1 3 4c0-.6.4-1 1-1h3.5c.6 0 1 .4 1 1 0 1.3.2 2.5.6 3.6.1.3 0 .7-.2 1z"/></svg>
          5307218394
        </li>
        <li class="contact-item">
          <svg viewBox="0 0 24 24"><path d="M2 4h20v16H2zm2 2v.5l8 5 8-5V6zm0 3v9h16V9l-8 5z"/></svg>
          Dispatcher@PipeworksTopMark.example
        </li>
        <li class="contact-item">
          <svg viewBox="0 0 24 24"><path d="M12 2a10 10 0 1 0 0 20 10 10 0 0 0 0-20zm6.9 6h-2.9a15 15 0 0 0-1.4-3.6A8 8 0 0 1 18.9 8zM12 4c.8 1.2 1.5 2.5 1.9 4h-3.8c.4-1.5 1.1-2.8 1.9-4zM4.3 14a8 8 0 0 1 0-4h3.4a16 16 0 0 0 0 4zm.8 2h2.9c.3 1.3.8 2.5 1.4 3.6A8 8 0 0 1 5.1 16zM8 8H5.1a8 8 0 0 1 4.3-3.6C8.8 5.5 8.3 6.7 8 8zm4 12c-.8-1.2-1.5-2.5-1.9-4h3.8c-.4 1.5-1.1 2.8-1.9 4zm2.3-6H9.7a14 14 0 0 1 0-4h4.6a14 14 0 0 1 0 4zm.3 5.6c.6-1.1 1.1-2.3 1.4-3.6h2.9a8 8 0 0 1-4.3 3.6zm1.7-5.6a16 16 0 0 0 0-4h3.4a8 8 0 0 1 0 4z"/></svg>
          www.PipeworksTopMark.example
        </li>
      </ul>
      <ul class="service-list">
        <li class="service-item">Sewer Drain Cleaning</li>
        <li class="service-item">Maintenance</li>
        <li class="service-item">Trenchless Pipe Installs.</li>
      </ul>
    </div>
  </section>
</body>
</html>
```